Simple Logo Design for Semi-Clear Plastic Frosted Card stock

Create a business card on frosted plastic. compliment existing logo elements with a tree trunk, roots, or seed at the lower half and the full logo both on the front.

Contact information will go on a solid portion of the back of this design since this card stock is semi-transparent.

It is important to consider this plastic card stock medium in your design. I found helpful tips and guides listed at vellaprint-sample.net: be careful to understand ink printed on plastic cards cannot have too much of a consistent print area or risks peeling and fine lines can easily scratch off.
Updates

2" x 3.5" 20PT Clear Plastic Business cards with Round corners Please get info or templates here: https://www.vellaprint-sample.net/product-detail/2-x-35-20pt-clear-plastic-business-cards-with-round-corners

Target Market(s)

Not for profit- religion

Industry/Entity Type

Business

Must include complementary elements to the existing logo

Font styles to use
Decorative

Colors
000000

Requirements
Must have
• Elements of community, nature and oneness. Such as: seed, roots, tree trunk, etc.
• Three lines of space on the back for Name, Title, Phone Number.
Nice to have
• I like a light use of decorative elements
Should not have
• No eyes, from faces or animals.

```html
<!DOCTYPE html>
<html lang="en">
<head>
<meta charset="utf-8">
<title>Steadfast Grove – Frosted Business Card</title>
<link href="https://fonts.googleapis.com/css2?family=Open+Sans:wght@400;600&family=Questrial&display=swap" rel="stylesheet">
<style>
  :root {
    --backdrop: #e8e5e1;
    --frost: #f3f3f1;
    --frost-edge: #d9dad7;
    --teal: #226e6a;
    --green: #4a9a40;
    --white: #ffffff;
  }
  html, body {
    margin: 0;
    padding: 0;
    width: 1200px;
    height: 900px;
    overflow: hidden;
    background: var(--backdrop);
  }
  .canvas {
    display: block;
    width: 1200px;
    height: 900px;
  }
  .card-body { fill: var(--frost); stroke: var(--frost-edge); stroke-width: 1; }
  .band-teal { fill: var(--teal); }
  .band-green { fill: var(--green); }
  .window { fill: var(--frost); }
  .ring-teal { fill: none; stroke: var(--teal); stroke-width: 6; }
  .ring-green { fill: none; stroke: var(--green); stroke-width: 6; }
  .holder-name {
    font-family: "Open Sans", sans-serif;
    font-weight: 600;
    font-size: 22px;
    fill: var(--white);
  }
  .holder-title, .holder-phone {
    font-family: "Open Sans", sans-serif;
    font-weight: 400;
    font-size: 15px;
    fill: var(--white);
  }
  .brand-name {
    font-family: "Questrial", sans-serif;
    font-size: 34px;
    letter-spacing: 1px;
    fill: var(--teal);
  }
  .brand-name--through {
    opacity: 0.3;
  }
  .phone-icon { fill: var(--white); }
</style>
</head>
<body>
<svg class="canvas" viewBox="0 0 1200 900" xmlns="http://www.w3.org/2000/svg">
  <defs>
    <clipPath id="front-clip"><rect x="78" y="35" width="582" height="360" rx="8"/></clipPath>
    <clipPath id="back-clip"><rect x="390" y="505" width="565" height="353" rx="8"/></clipPath>
  </defs>

  <!-- Front of card -->
  <g class="card card--front">
    <rect class="card-body" x="78" y="35" width="582" height="360" rx="8"/>
    <g clip-path="url(#front-clip)">
      <rect class="band-teal" x="78" y="35" width="400" height="98"/>
      <rect class="band-green" x="78" y="297" width="400" height="98"/>
      <circle class="window" cx="470" cy="213" r="187"/>
      <path class="ring-teal" d="M283,213 A187,187 0 0 1 657,213"/>
      <path class="ring-green" d="M657,213 A187,187 0 0 1 283,213"/>
    </g>
    <text class="holder-name" x="108" y="83">Daniel Whitford</text>
    <text class="holder-title" x="108" y="105">Managing Director</text>
    <path class="phone-icon" d="M112,344 c1,-1 3,-1 3,0 l2,3 c0,1 0,2 -1,2 c1,2 2,3 4,4 c0,-1 1,-1 2,-1 l3,2 c1,0 1,2 0,3 c-2,2 -5,1 -8,-2 c-3,-3 -5,-7 -5,-11 z"/>
    <text class="holder-phone" x="126" y="356">(055)-318-2046</text>
    <text class="brand-name" x="470" y="253" text-anchor="middle">STEADFAST GROVE</text>
  </g>

  <!-- Back of card -->
  <g class="card card--back">
    <rect class="card-body" x="390" y="505" width="565" height="353" rx="8"/>
    <g clip-path="url(#back-clip)">
      <rect class="band-teal" x="600" y="505" width="355" height="100"/>
      <rect class="band-green" x="600" y="762" width="355" height="96"/>
      <circle class="window" cx="577" cy="681" r="185"/>
      <path class="ring-teal" d="M392,681 A185,185 0 0 1 762,681"/>
      <path class="ring-green" d="M762,681 A185,185 0 0 1 392,681"/>
    </g>
    <text class="brand-name brand-name--through" x="-577" y="720" text-anchor="middle" transform="scale(-1,1)">STEADFAST GROVE</text>
  </g>
</svg>
</body>
</html>
```